Professional Website for Leading Global Private Equity Real Estate Company

The company is a leading global Private Equity Real Estate (PERE). We need a homepage design, an inner page design, and color/font tweaks to the logo (color should be more soothing than current blue used in the logo). The logo website should project the company as global, professional, experienced, trustworthy, accessible, YOUNG, DYNAMIC, hi-tech. PLEASE SEE the attached Design Brief Word Doc for details.

Target Market(s)

institional investors and wealthy private individuals

Industry/Entity Type

Finance

Number of Pages Required

2 page

Font styles to use
Sans Serif
Other font styles liked:
• either like in https://www.ferndalequay.com/ or like in presentations (Montserrat Black & Montserrat Light, Century Gothic, Blair ITC, Almoni Neue DL 4.0 AAA Medium, Almoni DL AAA)

Requirements
Must have
• new color palette that is NOT based on current logo. they want a more soothing color palette than the blue in that logo. the new color palette should project: global, professional, experienced, trustworthy, accessible, YOUNG, DYNAMIC, hi-tech.
Nice to have
• the likes these sites: https://www.ferndalequay.com/ and https://www.tvr.law/

```html
<!DOCTYPE html>
<html lang="en">
<head>
<meta charset="utf-8">
<title>Veridane Real Estate</title>
<link href="https://fonts.googleapis.com/css2?family=Jost:wght@300;400;500;600;700&family=Montserrat:wght@400;500;600;700&display=swap" rel="stylesheet">
<style>
:root{
  --navy:#1b3f70;
  --navy-deep:#0f2a52;
  --blue:#0d4fa3;
  --ink:#23344d;
  --text:#4a5565;
  --muted:#8a93a0;
  --light:#f1f2f4;
  --line:#d4d8de;
  --white:#ffffff;
}
*{margin:0;padding:0;box-sizing:border-box}
html,body{width:1200px;height:4167px;overflow:hidden}
body{position:relative;background:var(--white);font-family:"Jost",sans-serif;color:var(--text)}
.abs{position:absolute}
.center{left:0;width:1200px;text-align:center}
.title{font-family:"Jost",sans-serif;font-weight:300;font-size:38px;color:var(--ink);letter-spacing:.5px;text-transform:uppercase}
.title b{font-weight:600}
.rule{width:56px;height:4px;background:var(--blue)}
.rule.c{left:572px}
.btn-outline{display:flex;align-items:center;justify-content:center;border:2px solid var(--blue);color:var(--blue);font-family:"Montserrat",sans-serif;font-weight:700;font-size:15px;letter-spacing:.5px;text-transform:uppercase;background:var(--white)}
.body-text{font-size:15px;line-height:24px;color:var(--text)}
.photo{position:absolute}

/* hero */
.hero{left:0;top:0;width:1200px;height:705px;background:linear-gradient(180deg,#0c1f3d 0%,#1d3f6e 38%,#3a4e6a 62%,#5d4a3a 82%,#2a3a58 100%)}
.nav{position:absolute;top:0;left:0;width:1200px;height:90px}
.brand{position:absolute;left:102px;top:22px;display:flex;align-items:center;gap:12px;color:var(--white);font-family:"Montserrat",sans-serif;font-weight:500;font-size:19px;letter-spacing:1px;line-height:22px;text-transform:uppercase}
.brand i{width:40px;height:40px;border-radius:50%;background:var(--white);display:block}
.menu{position:absolute;top:36px;left:361px;display:flex;gap:0;font-family:"Montserrat",sans-serif;font-size:13px;font-weight:500;color:var(--white);text-transform:uppercase}
.menu span{margin-right:28px}
.login{position:absolute;left:989px;top:24px;width:116px;height:38px;border:2px solid var(--white);color:var(--white);font-family:"Montserrat",sans-serif;font-size:14px;display:flex;align-items:center;justify-content:center}
.hero h1{position:absolute;left:0;width:1200px;top:272px;text-align:center;color:var(--white);font-weight:300;font-size:56px;line-height:56px}
.hero h1 b{font-weight:600;display:block}
.play{position:absolute;left:584px;top:214px}
.hero-btn{position:absolute;left:519px;top:409px;width:173px;height:45px;background:var(--blue);color:var(--white);font-family:"Montserrat",sans-serif;font-weight:700;font-size:15px;display:flex;align-items:center;justify-content:center}

/* about */
.about{left:0;top:705px;width:1200px;height:589px;background:linear-gradient(180deg,#f4f4f5 0%,#eeeff1 60%,#c9cdd3 100%)}
.stat{position:absolute;top:1017px;width:230px;height:126px;text-align:center;padding-top:26px}
.stat strong{display:block;font-family:"Jost",sans-serif;font-weight:600;font-size:38px;color:var(--blue);line-height:40px}
.stat span{display:block;margin-top:6px;font-family:"Montserrat",sans-serif;font-weight:700;font-size:14px;color:var(--ink);text-transform:uppercase}
.stat.active{background:var(--blue)}
.stat.active strong,.stat.active span{color:var(--white)}

/* platforms */
.card{position:absolute;top:1475px;width:240px;height:266px;display:flex;flex-direction:column;justify-content:flex-end;align-items:center;padding-bottom:18px;text-align:center;color:var(--white);font-family:"Montserrat",sans-serif;font-weight:700;font-size:14px;line-height:19px;text-transform:uppercase}
.card.active{top:1455px;height:306px;background:var(--blue);justify-content:center;padding:0 24px}
.card.active p{font-family:"Jost",sans-serif;font-weight:400;text-transform:none;font-size:13px;line-height:17px;color:#c9d8ee;margin:10px 0 14px}
.card.active em{font-style:normal;border:2px solid var(--white);padding:7px 26px;font-size:11px}

/* subscribe */
.field{position:absolute;height:51px;background:var(--white);border:1px solid var(--line);font-family:"Montserrat",sans-serif;font-size:12px;color:var(--muted);display:flex;align-items:center;padding-left:20px}
.field.dark{border:none;font-size:13px;color:#7d8796}
.solid-btn{position:absolute;background:var(--blue);color:var(--white);font-family:"Montserrat",sans-serif;font-weight:700;font-size:15px;display:flex;align-items:center;justify-content:center}

/* footer */
.foot-h{position:absolute;top:3848px;font-family:"Montserrat",sans-serif;font-weight:600;font-size:15px;color:var(--ink);text-transform:uppercase}
.foot-list{position:absolute;top:3888px;list-style:none;font-size:13px;line-height:27px;color:var(--ink)}
.contact-row{position:absolute;left:847px;display:flex;align-items:flex-start;gap:14px;font-size:13px;color:var(--ink);line-height:16px}
.dot{width:28px;height:28px;border-radius:50%;background:var(--navy);flex:none;display:flex;align-items:center;justify-content:center}
.social{position:absolute;left:857px;top:4022px;display:flex;gap:6px}
.social i{width:28px;height:28px;border-radius:50%;border:3px solid #8c97a8;display:block}
.legal{position:absolute;top:4122px;font-size:12px;color:var(--ink)}
</style>
</head>
<body>

<section class="abs hero" role="img" aria-label="Night skyline of a financial district with lit towers"></section>
<nav class="nav">
  <div class="brand"><i></i><div>Veridane<br>Real Estate</div></div>
  <div class="menu"><span>About Us ⌄</span><span>Our Businesses ⌄</span><span>Investors Lobby</span><span>News</span><span>Contact Us</span></div>
  <div class="login">LOG IN</div>
</nav>
<svg class="play" width="54" height="54" viewBox="0 0 54 54"><circle cx="27" cy="27" r="25" fill="none" stroke="#fff" stroke-width="2.5"/><path d="M21 16 L38 27 L21 38 Z" fill="#fff"/></svg>
<h1 class="hero-title" style="position:absolute;left:0;width:1200px;top:278px;text-align:center;color:#fff;font-weight:300;font-size:56px;line-height:56px">Leading Global Private<b style="font-weight:600;display:block">Equity Real Estate</b></h1>
<div class="hero-btn">ABOUT US ›</div>

<section class="abs about"></section>
<h2 class="abs center title" style="top:790px">About <span style="font-weight:300"></span><b style="font-weight:600;position:absolute;opacity:0"></b></h2>
<h2 class="abs center title" style="top:790px;background:transparent"></h2>
<div class="abs rule c" style="top:842px"></div>
<p class="abs body-text" style="left:200px;width:800px;top:872px;text-align:center;font-size:16px;line-height:28px">Lorem ipsum dolor sit amet, consectetur adipiscing elit, sed do eiusmod tempor incididunt ut labore et dolore magna aliqua. Ut enim ad minim veniam, quis nostrud exercitation ullamco laboris nisi ut aliquip ex ea commodo consequat. Duis aute irure dolor in reprehenderit in voluptate ve</p>
<div class="stat" style="left:123px"><strong>$250</strong><span>Real Estate Projects</span></div>
<div class="stat active" style="left:378px"><strong>$25B</strong><span>Private Equity</span></div>
<div class="stat" style="left:640px"><strong>$25B</strong><span>Fund Solutions</span></div>
<div class="stat" style="left:879px"><strong>$120B</strong><span>Credit &amp; Insurance</span></div>

<h2 class="abs center title" style="top:1352px"><b>Our Investment</b> Platforms</h2>
<div class="abs rule c" style="top:1404px"></div>
<div class="card" style="left:0;background:linear-gradient(160deg,#5a6f8c,#3a3532)" role="img" aria-label="Hand touching a private equity data screen"><span>Sed ut perspiciatis<br>unde omnis</span></div>
<div class="card active" style="left:238px"><span>Sed ut perspiciatis<br>unde omnis</span><p>Lorem ipsum dolor sit amet, consectetur adipiscing elit, sed do eiusmod tempor incididunt ut labore et</p><em>Learn More</em></div>
<div class="card" style="left:479px;background:linear-gradient(180deg,#c9d1da,#5d6770 70%,#3b434c)" role="img" aria-label="Modern glass office building"><span>Vatem quia voluptas<br>sit aspernatur</span></div>
<div class="card" style="left:719px;background:linear-gradient(180deg,#7fa6cf,#3d5a7e 70%,#2c3a52)" role="img" aria-label="Businessman facing a connected city skyline"><span>Sed ut perspiciatis<br>unde omnis</span></div>
<div class="card" style="left:960px;width:240px;background:linear-gradient(180deg,#9aa2a8,#5e666c 70%,#353b40)" role="img" aria-label="Dense city towers seen from above"><span>Nemo enim ipsam<br>voluptatem</span></div>

<h2 class="abs title" style="left:121px;top:1902px;font-size:40px;text-transform:uppercase">Our <b>Edge</b></h2>
<p class="abs body-text" style="left:121px;top:1982px;width:430px">Lorem ipsum dolor sit amet, consectetur adipiscing elit, sed do eiusmod tempor incididunt ut co laboris nisi ut aliquip ex ea commodo consequat. Duis aute irure dolor in reprehende</p>
<p class="abs body-text" style="left:121px;top:2066px;width:430px">Aabor et dolore magna aliqua. Ut enim ad minim veniam, quis nostrud exercitation ullamco laboris nisi ut aliquip ex ea commodo consequat. Duis aute irure dolor in reprehenderitd exercitation.na aliqua. Ut enim ad minim veniam.</p>
<div class="abs btn-outline" style="left:121px;top:2194px;width:267px;height:54px">Investor Information</div>
<div class="abs" style="left:618px;top:1838px;width:600px;height:410px;border:3px solid var(--navy)"></div>
<div class="photo" style="left:632px;top:1851px;width:568px;height:458px;background:linear-gradient(170deg,#3f7fd6 0%,#7fb0ea 45%,#c8d6e8 75%,#6f8a7a 100%)" role="img" aria-label="Two glass skyscrapers against a blue sky"></div>

<section class="abs" style="left:0;top:2387px;width:1200px;height:357px;background:linear-gradient(180deg,#efefef,#e3e5e8 60%,#d3d7dc)"></section>
<h2 class="abs center title" style="top:2460px"><b>Stay</b> Updated</h2>
<div class="abs rule c" style="top:2509px"></div>
<p class="abs center body-text" style="top:2534px;font-size:17px">Get our latest insights, firm announcements and Charitable Foundation updates.</p>
<div class="field" style="left:226px;top:2594px;width:288px">NAME*</div>
<div class="field" style="left:526px;top:2594px;width:287px">EMAIL*</div>
<div class="solid-btn" style="left:823px;top:2594px;width:157px;height:51px">SUBSCRIBE</div>

<div class="photo" style="left:0;top:2744px;width:597px;height:526px;background:linear-gradient(160deg,#9aa39f 0%,#c9ccc9 40%,#6b6a66 75%,#3d3a36 100%)" role="img" aria-label="Team of colleagues discussing work at a laptop in an office"></div>
<h2 class="abs title" style="left:682px;top:2853px;font-size:40px">Our <b>Responsibility</b></h2>
<div class="abs rule" style="left:689px;top:2903px"></div>
<p class="abs body-text" style="left:687px;top:2930px;width:430px">Lorem ipsum dolor sit amet, consectetur adipiscing elit, sed do eiusmod tempor incididunt ut</p>
<p class="abs body-text" style="left:687px;top:2990px;width:430px">Aabor et dolore magna aliqua. Ut enim ad minim veniam, quis nostrud exercitation ullamco laboris nisi ut aliquip ex ea commodo consequat. Duis aute irure dolor in reprehenderitd exercitationna aliqua. Ut enim ad minim veniam.</p>
<div class="abs btn-outline" style="left:689px;top:3111px;width:166px;height:49px">Learn More</div>

<section class="abs" style="left:0;top:3270px;width:1200px;height:519px;background:var(--navy)"></section>
<h2 class="abs center title" style="top:3343px;color:var(--white)">Get <b>In Touch</b></h2>
<div class="abs rule c" style="top:3393px;background:var(--white)"></div>
<div class="field dark" style="left:288px;top:3430px;width:320px;height:40px;text-transform:none">First Name</div>
<div class="field dark" style="left:619px;top:3430px;width:320px;height:40px">Last Name</div>
<div class="field dark" style="left:288px;top:3481px;width:320px;height:40px">Phone Number</div>
<div class="field dark" style="left:619px;top:3481px;width:320px;height:40px">Email address</div>
<div class="field dark" style="left:288px;top:3531px;width:651px;height:80px;align-items:flex-start;padding-top:10px">Message</div>
<div class="abs" style="left:519px;top:3633px;width:209px;height:49px;border:2px solid var(--white);color:var(--white);font-family:Montserrat,sans-serif;font-weight:700;font-size:15px;display:flex;align-items:center;justify-content:center">SUBMIT MESSAGE</div>

<div class="abs" style="left:307px;top:3789px;width:1px;height:310px;background:var(--line)"></div>
<div class="abs" style="left:784px;top:3789px;width:1px;height:310px;background:var(--line)"></div>
<div class="foot-h" style="left:124px">Important Links</div>
<ul class="foot-list" style="left:129px"><li>About Us</li><li>Our Businesses</li><li>Investor Lobby</li><li>News</li><li>Contact Us</li></ul>
<div class="foot-h" style="left:355px">Explore Veridane Real Estate</div>
<ul class="foot-list" style="left:357px"><li>Private Equity</li><li>Real Estate</li><li>Credit</li><li>Strategic Partners</li><li>Tactical Opportunities</li><li>Infrastructure</li></ul>
<ul class="foot-list" style="left:559px"><li>Insurance Solutions</li><li>Life Sciences</li><li>Portfolio Operations</li><li>Technology and Innovations</li><li>Registered Products</li></ul>
<div class="foot-h" style="left:847px">Contact Details</div>
<div class="contact-row" style="top:3887px;left:852px"><span class="dot"><svg width="12" height="16" viewBox="0 0 12 16"><path d="M6 0a6 6 0 0 0-6 6c0 4.5 6 10 6 10s6-5.5 6-10a6 6 0 0 0-6-6zm0 8.5A2.5 2.5 0 1 1 6 3.5a2.5 2.5 0 0 1 0 5z" fill="#fff"/></svg></span><span>48 Harbor Crest Way Suite B<br>Bay Point, FL 33999</span></div>
<div class="contact-row" style="top:3940px;left:852px"><span class="dot"><svg width="14" height="14" viewBox="0 0 14 14"><path d="M3 0l2.5 3.5-1.5 1.8a8 8 0 0 0 4.7 4.7l1.8-1.5L14 11l-1.5 2.5C6 14 0 8 .5 1.5z" fill="#fff"/></svg></span><span style="font-size:15px;font-weight:500;line-height:28px">555-014-2290</span></div>
<div class="contact-row" style="top:3974px;left:852px"><span class="dot"><svg width="14" height="10" viewBox="0 0 14 10"><rect x=".5" y=".5" width="13" height="9" fill="none" stroke="#fff"/><path d="M.5.5 7 6 13.5.5" fill="none" stroke="#fff"/></svg></span><span style="color:var(--blue);line-height:28px">hello@veridanerealty.com</span></div>
<div class="social"><i></i><i></i><i></i><i></i></div>

<div class="abs" style="left:0;top:4099px;width:1200px;height:1px;background:var(--line)"></div>
<div class="legal" style="left:118px">Copyright © 2022 Veridane Realestate</div>
<div class="legal" style="left:834px">Terms of Use &nbsp;|&nbsp; Sitemap &nbsp;|&nbsp; Privacy Policy</div>

<style>
h2.title:nth-of-type(1){}
</style>
<div class="abs center title" style="top:790px;background:linear-gradient(180deg,#f4f4f5,#f2f3f4);height:46px"><b>About</b> Veridane Real Estate</div>
</body>
</html>
```